Need CATCHY/VIVID Banner design for my new UTV/ATV/Off Road Vehicle turn signal/lighting company

I need a banner ad designed so I can advertise on several different ATV (all terrain vehicle), UTV (Utility Vehicles), Golf Cart and Off-Road Vehicle forums. Ads need to be very catchy and produce a call to action. Action is getting hits to my website. Our main business is selling turn signal kits to make your side by side or your ATV/UTV street legal, as some states now allow you to drive these on public roads if you have the following items: Turn Signals, Horn, Lighted license plate bracket, headlights and brake lights. We sell all of these items for just about any model vehicle out there. Our call to action for this banner would be to get more website visits.

Target Market(s)

Off-road/outdoor enthusiasts,

Industry/Entity Type

Car Accessorie

Font styles to use
Sans Serif

Requirements
Must have
• Ad size need to be either 728x90 or 300x250. Colorful ad with an off-road vehicle integrated to the design (think UTV, side-by-side, etc.
Nice to have
• Nice to haves would be anything that makes this banner ad stand out on very boring web pages.
Should not have
• anything dull

```html
<!DOCTYPE html>
<html lang="en">
<head>
<meta charset="utf-8">
<title>Trailmark – ATV Vehicle Signal Lighting</title>
<link rel="stylesheet" href="https://fonts.googleapis.com/css2?family=Montserrat:wght@600;700;800&display=swap">
<style>
  :root {
    --navy: #1d222c;
    --navy-soft: #262c38;
    --red: #e4212a;
    --red-deep: #c8161f;
    --yellow: #f6c21a;
    --white: #ffffff;
    --sky: #b9cfe0;
    --rock: #b8916a;
    --rock-dark: #6f5440;
  }
  * { margin: 0; padding: 0; box-sizing: border-box; }
  html, body { width: 1200px; height: 1000px; overflow: hidden; background: var(--navy); }
  .banner {
    position: relative; width: 1200px; height: 1000px; overflow: hidden;
    font-family: "Montserrat", Arial, sans-serif; color: var(--white);
  }
  .scene-photo {
    position: absolute; inset: 0;
    background: linear-gradient(180deg, var(--sky) 0%, #d7c4a6 30%, var(--rock) 55%, var(--rock-dark) 100%);
  }
  .panel { position: absolute; inset: 0; width: 1200px; height: 1000px; }
  .brand {
    position: absolute; top: 70px; left: 0; width: 560px;
    display: flex; align-items: center; justify-content: center; gap: 16px;
    font-weight: 800; font-size: 58px; letter-spacing: 2px; color: var(--red);
  }
  .brand-dot { width: 34px; height: 34px; border-radius: 50%; background: var(--yellow); }
  .tagline { position: absolute; left: 40px; top: 178px; font-weight: 800; line-height: 1; }
  .tagline-main { font-size: 41px; letter-spacing: 0.5px; }
  .tagline-sub { font-size: 26px; margin-top: 12px; letter-spacing: 0.3px; }
  .headline {
    position: absolute; left: 40px; top: 294px; font-weight: 800;
    font-size: 54px; line-height: 70px; letter-spacing: 0.5px;
  }
  .features { position: absolute; left: 64px; top: 458px; display: flex; gap: 62px; align-items: center; }
  .features svg { width: 72px; height: 56px; }
  .cta {
    position: absolute; left: 38px; top: 544px; width: 366px; height: 90px;
    border-radius: 45px; background: var(--red);
    display: flex; align-items: center; justify-content: center; gap: 22px;
    font-weight: 800; font-size: 29px; letter-spacing: 0.5px; color: var(--white);
    text-decoration: none; box-shadow: 0 6px 14px rgba(0,0,0,0.35);
  }
  .cta svg { width: 48px; height: 48px; }
</style>
</head>
<body>
<main class="banner">
  <div class="scene-photo" role="img" aria-label="Photo of a red and black side-by-side UTV climbing desert boulders under a blue sky with mountains behind"></div>

  <svg class="panel" viewBox="0 0 600 500" preserveAspectRatio="none" aria-hidden="true">
    <defs>
      <radialGradient id="panelShade" cx="0.2" cy="0.3" r="0.8">
        <stop offset="0" stop-color="#2a303c"/>
        <stop offset="1" stop-color="#1b2029"/>
      </radialGradient>
    </defs>
    <circle cx="60" cy="150" r="300" fill="var(--yellow)"/>
    <circle cx="84" cy="124" r="288" fill="var(--red)"/>
    <circle cx="80" cy="120" r="275" fill="url(#panelShade)"/>
  </svg>

  <div class="brand"><span class="brand-dot"></span>TRAILMARK</div>

  <div class="tagline">
    <div class="tagline-main">TURN SIGNAL KITS</div>
    <div class="tagline-sub">&amp; LIGHTING ACCESSORIES</div>
  </div>

  <h1 class="headline">ATV VECHICLE<br>SIGNAL LIGHTING</h1>

  <div class="features" aria-label="Brake lights, headlights, horn, turn signals">
    <svg viewBox="0 0 72 56" fill="none" stroke="var(--white)" stroke-width="4" stroke-linecap="round">
      <circle cx="36" cy="28" r="17"/>
      <path d="M13 12 A24 24 0 0 0 13 44 M59 12 A24 24 0 0 1 59 44"/>
      <line x1="36" y1="18" x2="36" y2="31"/>
      <circle cx="36" cy="38" r="1.5" fill="var(--white)"/>
    </svg>
    <svg viewBox="0 0 72 56" fill="var(--white)">
      <path d="M34 10 C14 10 10 20 10 28 C10 36 14 46 34 46 Z"/>
      <g stroke="var(--white)" stroke-width="4" stroke-linecap="round">
        <line x1="44" y1="16" x2="62" y2="16"/><line x1="44" y1="24" x2="62" y2="24"/>
        <line x1="44" y1="32" x2="62" y2="32"/><line x1="44" y1="40" x2="62" y2="40"/>
      </g>
    </svg>
    <svg viewBox="0 0 72 56" fill="var(--white)">
      <path d="M22 24 L46 14 L46 42 L22 32 Z"/>
      <rect x="14" y="22" width="10" height="12" rx="2"/>
      <g stroke="var(--white)" stroke-width="3" stroke-linecap="round">
        <line x1="4" y1="28" x2="10" y2="28"/><line x1="5" y1="18" x2="10" y2="21"/>
        <line x1="5" y1="38" x2="10" y2="35"/><line x1="8" y1="10" x2="12" y2="15"/>
        <line x1="8" y1="46" x2="12" y2="41"/>
      </g>
    </svg>
    <svg viewBox="0 0 72 56" fill="none" stroke="var(--white)" stroke-width="4" stroke-linejoin="round">
      <path d="M4 28 L20 12 L20 21 L32 21 L32 35 L20 35 L20 44 Z"/>
      <path d="M68 28 L52 12 L52 21 L40 21 L40 35 L52 35 L52 44 Z"/>
    </svg>
  </div>

  <a class="cta" href="#">LEARN MORE
    <svg viewBox="0 0 48 48" fill="none" stroke="var(--white)" stroke-width="4" stroke-linecap="round" stroke-linejoin="round">
      <circle cx="24" cy="24" r="20"/>
      <path d="M20 15 L29 24 L20 33"/>
    </svg>
  </a>
</main>
</body>
</html>
```